Overview of Elder Abuse Resources Brochure

We need a 2-page brochure that provides a list of resources for elders in tribal communities in the US and those who care for them. We want it to be simple and easy to read, and easy to see the difference between each resource. We would also like eye-catching images or graphics. Please keep the images on the front, and add any photos or graphics that depict Native American elders. We need both of our logos on the first page, in the far-right column. Please refer to the attached image for our brand colors and a font suggestion. Please keep the three columns on each page, but delete the blank pages in the document.

```html
<!DOCTYPE html>
<html lang="en">
<head>
<meta charset="utf-8">
<title>Services for Elders &amp; People Who Care for Them – Brochure</title>
<link rel="stylesheet" href="https://fonts.googleapis.com/css2?family=Barlow:wght@400;500;600;700&family=Barlow+Semi+Condensed:wght@500;600;700&display=swap">
<style>
:root{
  --teal:#2a7a80;
  --teal-light:#41b6c4;
  --rust:#bb5a4b;
  --maroon:#4b1b18;
  --maroon-deep:#3b1412;
  --navy:#14243a;
  --ink:#222;
  --muted:#9a9a9a;
  --rule:#d6d6d6;
  --bg:#d9d9d9;
  --white:#fff;
}
*{box-sizing:border-box;margin:0;padding:0}
html,body{width:1200px;height:2336px;overflow:hidden}
body{background:var(--bg);font-family:"Barlow",sans-serif;color:var(--ink);position:relative}
.page{position:absolute;left:30px;width:1140px;height:806px;background:var(--white);box-shadow:0 6px 18px rgba(0,0,0,.25);overflow:hidden}
.page--outside{top:322px}
.page--inside{top:1208px}
.panel{position:absolute;top:0;width:380px;height:790px}
.panel:nth-child(1){left:0}.panel:nth-child(2){left:380px}.panel:nth-child(3){left:760px}
.edge-band{position:absolute;left:0;bottom:0;width:100%;height:16px;background:linear-gradient(90deg,#7fb9bd,#d7a39a,#7fb9bd,#d7a39a,#7fb9bd)}
.heading{font-family:"Barlow Semi Condensed",sans-serif;font-weight:700;text-transform:uppercase;line-height:1.05}
.t-teal{color:var(--teal)}.t-rust{color:var(--rust)}

/* Respect panel */
.respect{padding:36px 38px 0}
.respect .heading{font-size:34px;margin-bottom:18px}
.respect p{font-size:15.5px;line-height:1.3;margin-bottom:18px}
.help-box{margin-top:12px;border:1px solid #bbb}
.help-box__title{background:var(--rust);color:#fff;text-align:center;font-family:"Barlow Semi Condensed",sans-serif;font-weight:600;font-size:22px;padding:4px 0}
.help-box__sub{background:var(--teal);color:#fff;text-align:center;font-size:15.5px;line-height:1.3;padding:7px 20px}
.help-box__blank{height:98px;color:#aaa;text-align:center;font-size:15px;line-height:1.3;padding:20px 40px 0}
.help-list{margin-top:18px}
.help-list li{list-style:none;text-align:center;font-size:15.5px;line-height:1.25;padding:9px 0;border-bottom:1px solid var(--rule)}
.help-list li:last-child{border-bottom:0}
.help-list .big{font-family:"Barlow Semi Condensed",sans-serif;font-size:19px;font-weight:700;color:var(--teal)}
.help-list .em{color:var(--rust);font-weight:600}
.help-list .strong{font-size:18px;font-weight:600}

/* Mailer panel */
.mailer{background:var(--teal);color:#fff}
.vtext{position:absolute;writing-mode:vertical-rl;transform:rotate(180deg);font-size:15px;line-height:1.2;white-space:nowrap}
.vtext b{font-weight:700}
.mailer__org{top:45px;left:310px;font-family:"Barlow Semi Condensed",sans-serif;font-weight:700;font-size:19px;line-height:1.1;text-transform:uppercase;height:190px}

/* Cover */
.cover__brand{height:118px;display:flex;align-items:center;gap:12px;padding:0 32px}
.cover__brand-mark{width:40px;height:40px;border-radius:50%;background:var(--teal)}
.cover__brand-name{font-family:"Barlow Semi Condensed",sans-serif;font-weight:700;font-size:25px;line-height:1.05;color:var(--rust);text-transform:uppercase}
.trim{height:22px;background:linear-gradient(90deg,#e0b6ad,#f2e3df,#9ccbcf,#f2e3df,#e0b6ad)}
.cover__title{background:var(--maroon);height:186px;padding:20px 30px;color:#fff}
.cover__title h1{font-family:"Barlow Semi Condensed",sans-serif;font-weight:600;font-size:33px;line-height:1.1}
.cover__title p{font-size:11.5px;line-height:1.4;margin-top:12px;padding-top:6px;border-top:1px solid rgba(255,255,255,.25);width:215px}
.photo{background:linear-gradient(180deg,#6fa6d6 0%,#b9d2e6 35%,#c98a5e 60%,#8a4d33 100%)}
.cover__photo{height:266px}
.cover__foot{display:flex;padding:14px 22px 0 20px;gap:18px}
.cover__points{flex:1;list-style:none}
.cover__points li{display:flex;align-items:center;gap:12px;font-size:12px;line-height:1.3;padding:7px 0;border-bottom:1px solid var(--rule)}
.cover__points li:last-child{border-bottom:0}
.icon-dot{flex:none;width:34px;height:34px;border-radius:50%;background:var(--rust);display:flex;align-items:center;justify-content:center}
.partner{width:124px;height:124px;margin-top:12px;background:var(--navy);border:2px solid #c9a24a;display:flex;align-items:center;justify-content:center;text-align:center;padding:10px}
.partner span{font-family:"Barlow",sans-serif;font-weight:600;font-size:14px;color:#c9a24a;text-transform:uppercase;line-height:1.2}

/* Inside */
.stories{padding:36px 38px 0}
.stories .heading{font-size:28px;margin-bottom:26px}
.stories ul{list-style:none}
.stories li{display:flex;align-items:center;gap:16px;font-size:15px;line-height:1.3;margin-bottom:18px}
.tick{flex:none;width:17px;height:17px}
.stories__photo{position:absolute;left:0;top:492px;width:380px;height:298px;background:linear-gradient(180deg,#7a8f5b 0%,#a7a58a 40%,#b7a7b4 70%,#6f5a63 100%)}
.stories__trim{position:absolute;left:0;top:470px;width:380px;height:22px}

.resources{padding:36px 44px 0 46px;font-size:14.5px;line-height:1.28}
.resources .heading{font-size:28px;margin-bottom:18px}
.entry{padding-bottom:12px;margin-bottom:12px;border-bottom:1px solid var(--rule)}
.entry:last-child{border-bottom:0}
.entry h3{font-family:"Barlow",sans-serif;font-size:15.5px;font-weight:700;line-height:1.2}
.entry .line{font-weight:500}
.resources--elders{background:var(--maroon-deep);color:#fff}
.resources--elders .heading{color:#fff}
.resources--elders .entry{border-color:rgba(255,255,255,.25)}
.resources--elders h3{color:var(--teal-light)}
.resources--carers h3{color:var(--teal)}
.sub-heading{font-family:"Barlow Semi Condensed",sans-serif;font-weight:600;font-size:22px;line-height:1.15;color:var(--teal);margin-bottom:24px}
.section-title{font-family:"Barlow Semi Condensed",sans-serif;font-weight:600;font-size:27px;color:var(--rust);margin:8px 0 4px}
</style>
</head>
<body>

<!-- Outside spread -->
<section class="page page--outside">
  <div class="panel respect">
    <h2 class="heading"><span class="t-teal">Respect for</span> <span class="t-rust">Elders</span></h2>
    <p>Do you have concerns about an Elder, maybe you see that they are not taking care of themselves, or family only comes once a month when the Elder has money?</p>
    <p>Is an Elder telling you that they are not treated with respect or that someone is bothering them?</p>
    <p>These may be signs of Elder abuse, neglect or exploitation.</p>
    <div class="help-box">
      <div class="help-box__title">FOR HELP CONTACT</div>
      <div class="help-box__sub">Your Tribal Social Services or Elders Department:</div>
      <div class="help-box__blank">Insert contact information for your tribal services, law enforcement, etc.</div>
    </div>
    <ul class="help-list">
      <li>The Elder Help Finder for information<br>on Adult Protective Services<br><span class="big">1-800-555-0142</span></li>
      <li class="strong">If a serious emergency, <span class="em">call 911.</span></li>
      <li>For mental health support for yourself<br>or an Elder, <span class="em">call or text 1-800-555-0188</span></li>
      <li>Family Safety Hotline<br><span class="big">1.800.555.SAFE (7233)</span></li>
    </ul>
  </div>

  <div class="panel mailer">
    <div class="vtext mailer__org">Northern Circle Council<br>on Aging</div>
    <div class="vtext" style="left:42px;top:420px;height:130px"><b>Recipient</b><br>Street Address<br>City, ST ZIP Code</div>
    <div class="vtext" style="left:42px;top:630px;height:120px"><b>Company Name</b><br>Street Address<br>City, ST ZIP</div>
    <div class="vtext" style="left:312px;top:480px;height:70px">Website<br>Email</div>
    <div class="vtext" style="left:312px;top:680px;height:70px">Telephone<br>Fax</div>
  </div>

  <div class="panel cover">
    <div class="cover__brand">
      <span class="cover__brand-mark"></span>
      <span class="cover__brand-name">Northern Circle Council<br>on Aging</span>
    </div>
    <div class="trim"></div>
    <div class="cover__title">
      <h1>Services for Elders<br>&amp; People Who Care<br>for Them</h1>
      <p>My Mother | My Father | My Sister<br>My Grandchild | Myself</p>
    </div>
    <div class="trim"></div>
    <div class="photo cover__photo" role="img" aria-label="Photo of a Native American grandmother and young granddaughter seated outdoors before red desert buttes"></div>
    <div class="cover__foot">
      <ul class="cover__points">
        <li><span class="icon-dot"><svg width="16" height="18" viewBox="0 0 16 18"><circle cx="8" cy="5" r="4" fill="#fff"/><path d="M0 18c0-5 3.5-7 8-7s8 2 8 7z" fill="#fff"/></svg></span>Are you caring for an Elder<br>or a Grandchild?</li>
        <li><span class="icon-dot"><svg width="16" height="18" viewBox="0 0 16 18"><circle cx="8" cy="5" r="4" fill="#fff"/><path d="M0 18c0-5 3.5-7 8-7s8 2 8 7z" fill="#fff"/></svg></span>Are you an Elder who needs<br>help staying at home?</li>
        <li><span class="icon-dot"><svg width="16" height="18" viewBox="0 0 16 18"><circle cx="8" cy="5" r="4" fill="#fff"/><path d="M0 18c0-5 3.5-7 8-7s8 2 8 7z" fill="#fff"/></svg></span>These programs and<br>information can be a<br>helpful resource.</li>
      </ul>
      <div class="partner"><span>Elder Justice Circle</span></div>
    </div>
  </div>
  <div class="edge-band"></div>
</section>

<!-- Inside spread -->
<section class="page page--inside">
  <div class="panel stories">
    <h2 class="heading t-rust">Do these stories sound<br>familiar to you?</h2>
    <ul>
      <li><svg class="tick" viewBox="0 0 17 17"><circle cx="8.5" cy="8.5" r="8.5" fill="#41a7b3"/><path d="M4.5 8.8l2.7 2.6 5.2-5.4" stroke="#fff" stroke-width="2" fill="none"/></svg>My mother gets lost driving home from the store.</li>
      <li><svg class="tick" viewBox="0 0 17 17"><circle cx="8.5" cy="8.5" r="8.5" fill="#41a7b3"/><path d="M4.5 8.8l2.7 2.6 5.2-5.4" stroke="#fff" stroke-width="2" fill="none"/></svg>I need help getting groceries and with chores at home.</li>
      <li><svg class="tick" viewBox="0 0 17 17"><circle cx="8.5" cy="8.5" r="8.5" fill="#41a7b3"/><path d="M4.5 8.8l2.7 2.6 5.2-5.4" stroke="#fff" stroke-width="2" fill="none"/></svg>My dad wants to sleep all the time; he doesn’t go out with friends anymore. He stopped drumming.</li>
      <li><svg class="tick" viewBox="0 0 17 17"><circle cx="8.5" cy="8.5" r="8.5" fill="#41a7b3"/><path d="M4.5 8.8l2.7 2.6 5.2-5.4" stroke="#fff" stroke-width="2" fill="none"/></svg>My sister is raising 3 grandchildren on her own.</li>
      <li><svg class="tick" viewBox="0 0 17 17"><circle cx="8.5" cy="8.5" r="8.5" fill="#41a7b3"/><path d="M4.5 8.8l2.7 2.6 5.2-5.4" stroke="#fff" stroke-width="2" fill="none"/></svg>My son is disrespecting me. He only comes to visit when my retirement money arrives. He always asks for money.</li>
    </ul>
    <div class="trim stories__trim"></div>
    <div class="stories__photo" role="img" aria-label="Group photo of six Native American Elders standing together outdoors"></div>
  </div>

  <div class="panel resources resources--elders">
    <h2 class="heading">Resources for Elders</h2>
    <div class="entry">
      <h3>Elder Help Finder</h3>
      <div class="line">https://elderhelpfinder.example.org/home</div>
      <div class="line">Call or Text: 1-800-555-0142</div>
      <div class="line">Email: help@elderhelpfinder.example.org</div>
      For help finding support. Ask about services to Tribal Elders.
    </div>
    <div class="entry">
      <h3>Memory Care Call Line</h3>
      <div class="line">(24 hours 7 days a week)</div>
      <div class="line">Call 1-800-555-0173</div>
      For support for people living with dementia, caregivers, families and the public. Connect with a live person who can provide information, local resources, crisis assistance and emotional support.
    </div>
    <div class="entry">
      <h3>Crisis Care Lifeline</h3>
      For mental health support, <span class="line">call or text 1-800-555-0188.</span>
    </div>
    <div class="entry">
      <h3>State &amp; Tribal Hotlines | Elder Justice Circle</h3>
      To find local resources within your tribe or state that specialize in elder abuse, neglect or exploitation, visit:
      <div class="line">https://northerncircle.example.org/justice/ state-tribal-hotlines/</div>
    </div>
    <div class="entry">
      <h3>Red Cedar Native Helpline</h3>
      A 24/7 safe, confidential and anonymous domestic and sexual violence helpline for Native Americans and Alaska Natives.
      <div class="line">Call 1-844-555-0119 (1-844-5CEDAR)</div>
      <div class="line">https://redcedarhelpline.example.org/</div>
    </div>
  </div>

  <div class="panel resources resources--carers">
    <h2 class="heading t-rust" style="margin-bottom:8px">Resources for<br>Caregivers</h2>
    <div class="sub-heading">Caring for an Older Adult</div>
    <div class="entry">
      <h3>Elder Help Finder</h3>
      <div class="line">https://elderhelpfinder.example.org/home</div>
      <div class="line">Call or Text: 1-800-555-0142</div>
      <div class="line">Email: help@elderhelpfinder.example.org</div>
      For help finding support. Ask about services to Tribal Elders.
    </div>
    <div class="entry">
      <h3>Memory Friends | Northern Circle Council on Aging</h3>
      An interactive educational program to better understand what dementia is and how it affects people.
      <div class="line">https://northerncircle.example.org/memory-friends/</div>
    </div>
    <div class="section-title">Caring for a Grandchild</div>
    <div class="sub-heading" style="margin-bottom:18px">Grandparents Raising<br>Grandchildren (Kinship Care)</div>
    <div class="entry">
      <h3>Kinfamilies.example.org</h3>
      An interactive website that seeks to share all relevant publicly available information impacting grandfamilies.
    </div>
    <div class="entry">
      <h3>Grandparent Resources | Elder Justice Circle</h3>
      A list of resources for grandparents raising grandchildren.
      <div class="line">https://northerncircle.example.org/justice/ grandparent-resources/</div>
    </div>
  </div>
  <div class="edge-band"></div>
</section>

</body>
</html>
```